Vindgerdi - Start-up company selling electricity

Hello let me tell you about Vindgerdi.

Vindgerdi is start-up company selling electricity in Iceland. The operations of the company consist of making power usage forecasts for our customers, purchasing the electricity wholesale from the energy producers, and selling the electricity to the consumer. We are focused on tech by using optimization and machine learning to minimize electricity prices to our customers. Our marketing strategy is to portray a tech company mindset and to show dedication to driving down the electricity price on the market.

We need your help to make our website pop. Possible concepts to work with are as follows:

- Iceland the land of ice and fire
- Green energy
- Innovation
- Tech and data science

Link to our website: https://prufa.vindgerdi-example.is/
We are open to ideas.
Thank you!

Target Market(s)

Electricity consumers both homes and companies.

Number of Pages Required

1 page

Font styles to use
Serif
Sans Serif

```html
<!DOCTYPE html>
<html lang="en">
<head>
<meta charset="utf-8">
<title>Vindgerdi – Same electricity, just cheaper</title>
<link rel="stylesheet" href="https://fonts.googleapis.com/css2?family=Cinzel:wght@700&family=Crimson+Pro:wght@500;600&family=Poppins:wght@300;400;500;600&display=swap">
<style>
:root{
  --navy:#0b3467;
  --navy-deep:#082c5a;
  --navy-soft:#8a9bb6;
  --red:#9c2f33;
  --ink:#1a1a1a;
  --muted:#6b6b6b;
  --white:#ffffff;
  --footer-text:#d7deea;
}
*{box-sizing:border-box;margin:0;padding:0}
html,body{width:1200px;height:2786px;overflow:hidden}
body{position:relative;background:var(--white);font-family:'Poppins',sans-serif;color:var(--ink)}
.abs{position:absolute}

/* top bar */
.topbar{left:0;top:0;width:1200px;height:38px;background:var(--navy);color:var(--white);font-size:12px}
.topbar .welcome{left:62px;top:11px}
.topbar .info{top:10px;display:flex;align-items:center;gap:10px}
.topbar .badge{width:26px;height:26px;border-radius:50%;background:var(--white);display:flex;align-items:center;justify-content:center;margin-top:-4px}

/* header */
.header{left:0;top:38px;width:1200px;height:75px;background:var(--white)}
.brand{display:flex;align-items:center;gap:10px;font-family:'Crimson Pro',serif;font-weight:600;font-size:34px;color:var(--red);letter-spacing:.5px}
.brand .dot{width:30px;height:30px;border-radius:50%;background:var(--navy)}
.header .brand{left:60px;top:16px}
.nav{top:32px;font-size:12.5px;color:#555}
.nav.active{color:var(--red)}
.nav.active::after{content:"";position:absolute;left:50%;top:22px;width:10px;height:10px;margin-left:-5px;border-radius:50%;background:var(--navy)}
.pill{display:flex;align-items:center;justify-content:space-between;border-radius:30px;color:var(--white);font-size:14px;letter-spacing:.3px;padding:0 5px 0 16px}
.pill .knob{width:32px;height:32px;border-radius:50%;background:var(--white);display:flex;align-items:center;justify-content:center}
.pill .knob i{width:12px;height:12px;border-radius:50%;background:var(--navy);display:block}
.header .pill{left:978px;top:18px;width:162px;height:41px;background:var(--red)}

/* hero */
.hero-photo{left:0;top:113px;width:1200px;height:750px;
  background:
    linear-gradient(180deg,rgba(0,0,0,0) 55%,rgba(20,14,10,.85) 100%),
    linear-gradient(100deg,#6f6a2a 0%,#8a5a22 30%,#7c4420 60%,#5e2a1a 100%);
  clip-path:polygon(0 0,100% 0,100% 100%,0 73%)}
.hero-title{left:0;top:312px;width:1200px;text-align:center;font-family:'Cinzel',serif;font-weight:700;font-size:60px;color:var(--white);letter-spacing:1px}
.hero-sub{left:330px;top:384px;width:540px;text-align:center;font-size:14px;font-weight:500;line-height:23px;color:var(--white)}
.hero .pill{left:519px;top:438px;width:161px;height:40px;background:var(--navy)}

/* sections */
.lead{left:0;top:910px;width:1200px;text-align:center;font-family:'Crimson Pro',serif;font-weight:600;font-size:33px;color:var(--navy)}
.block-red{background:var(--red)}
.tone-block{background:var(--navy-soft);opacity:.55}
.frame{border:1.5px solid #c9c9c9}
.feature h2{font-family:'Crimson Pro',serif;font-weight:500;font-size:23px;color:#111;margin-bottom:8px}
.feature p{font-size:12.6px;line-height:19.5px;color:var(--muted);font-weight:300}
.btn{display:flex;align-items:center;justify-content:center;border-radius:22px;background:var(--navy);color:var(--white);font-size:14px;letter-spacing:.3px}
.price{text-align:center;color:var(--muted);font-size:12px;line-height:19px;font-weight:300}
.price strong{display:block;font-size:25px;color:var(--red);font-weight:600;line-height:30px}

/* footer */
.footer-bg{left:0;top:2276px;width:1200px;height:474px;background:var(--navy);clip-path:polygon(0 0,100% 42%,100% 100%,0 100%)}
.email{left:60px;top:2390px;width:284px;height:37px;border-radius:20px;background:var(--white);font-size:12px;color:#555;padding:11px 16px}
.submit{left:364px;top:2390px;width:134px;height:37px;border-radius:20px;background:var(--red);color:var(--white);font-size:14px;display:flex;align-items:center;justify-content:center}
.footer .brand{left:60px;top:2483px;font-size:30px}
.footer .brand .dot{width:24px;height:24px;background:var(--white)}
.about{left:61px;top:2543px;width:240px;font-size:12.5px;line-height:19.5px;color:var(--footer-text);font-weight:300}
.col-title{top:2484px;font-size:19px;font-weight:400;color:var(--white)}
.links{list-style:none;font-size:12.5px;color:var(--footer-text);font-weight:300}
.links li::before{content:"- "}
.contact-row{left:612px;display:flex;align-items:center;gap:13px;font-size:12px;color:var(--white)}
.contact-row .ico{width:34px;height:34px;background:var(--white);display:flex;align-items:center;justify-content:center}
.copyright{left:0;top:2749px;width:1200px;height:37px;background:var(--red);color:#f0d6d6;font-size:12px;text-align:center;padding-top:11px}
</style>
</head>
<body>

<div class="abs topbar">
  <span class="abs welcome">Welcome To VINDGERDI!</span>
  <div class="abs info" style="left:790px">
    <span class="badge"><svg width="14" height="14" viewBox="0 0 24 24"><path fill="#9c2f33" d="M6.6 10.8a15 15 0 0 0 6.6 6.6l2.2-2.2a1 1 0 0 1 1-.25 11.4 11.4 0 0 0 3.6.6 1 1 0 0 1 1 1V20a1 1 0 0 1-1 1A17 17 0 0 1 3 4a1 1 0 0 1 1-1h3.5a1 1 0 0 1 1 1c0 1.25.2 2.45.6 3.6a1 1 0 0 1-.25 1z"/></svg></span>
    <span>Call: 555-0199</span>
  </div>
  <div class="abs info" style="left:957px">
    <span class="badge"><svg width="14" height="14" viewBox="0 0 24 24"><rect x="2" y="5" width="20" height="14" rx="2" fill="#9c2f33"/><circle cx="8" cy="11" r="2.2" fill="#fff"/><rect x="12" y="9" width="7" height="1.6" fill="#fff"/><rect x="12" y="13" width="7" height="1.6" fill="#fff"/></svg></span>
    <span>ID Number: 123456-7890</span>
  </div>
</div>

<header class="abs header">
  <div class="abs brand"><span class="dot"></span>VINDGERDI</div>
  <a class="abs nav active" style="left:472px">Home</a>
  <a class="abs nav" style="left:541px">Terms of Business</a>
  <a class="abs nav" style="left:688px">Question &amp; Answer</a>
  <a class="abs nav" style="left:840px">About Vindgerdi</a>
  <a class="abs pill">CONTACT US <span class="knob"><i></i></span></a>
</header>

<section class="hero">
  <div class="abs hero-photo" role="img" aria-label="Photo: high-voltage transmission towers and power lines silhouetted against an orange sunset sky"></div>
  <h1 class="abs hero-title">VINDGERDI</h1>
  <p class="abs hero-sub">We are focused on tech by using optimization and machine learning to minimize electricity prices to our customers</p>
  <a class="abs pill">CONTACT US <span class="knob"><i></i></span></a>
</section>

<h2 class="abs lead">Same electricity ~ just cheaper!</h2>

<!-- welcome -->
<div class="abs block-red" style="left:221px;top:997px;width:223px;height:186px"></div>
<div class="abs tone-block" role="img" aria-label="Decorative diagonal line texture" style="left:158px;top:1107px;width:107px;height:150px"></div>
<div class="abs" role="img" aria-label="Photo: hands holding a tablet showing energy data in an industrial plant" style="left:264px;top:1030px;width:240px;height:303px;background:linear-gradient(160deg,#8a8f92 0%,#3c4448 45%,#2aa3a5 80%,#1f7f86 100%)"></div>
<div class="abs frame" style="left:247px;top:1169px;width:220px;height:184px"></div>
<div class="abs feature" style="left:643px;top:1019px;width:405px">
  <h2>Welcome to business</h2>
  <p>In the event of a dispute between Vindgerdi and the customer, the parties shall seek conciliation. If this is not the case, the customer can direct a complaint to the National Energy Authority. The customer can also file a complaint to the National Energy Authority if he considers that Vindgerdi is not fulfilling its obligations under the Electricity Act or related regulations.</p>
  <p style="margin-top:1px">f a customer moves and receives a new address during the contract period, this will lead to a change of user. Switching users means that the customer's (user) connection to the electricity system moves from one place to another.</p>
</div>
<a class="abs btn" style="left:642px;top:1268px;width:135px;height:37px">COMPANY</a>

<!-- price list -->
<div class="abs feature" style="left:160px;top:1464px;width:405px">
  <h2>Price List</h2>
  <p>f a customer moves and receives a new address during the contract period, this will lead to a change of user. Switching users means that the customer's (user) connection to the electricity system moves from one place to another.</p>
</div>
<div class="abs price" style="left:188px;top:1596px;width:80px"><strong>6.95</strong>ISK / kWh</div>
<div class="abs price" style="left:309px;top:1596px;width:140px"><strong>6.22</strong>ISK / kWh<br>electric acceleration</div>
<a class="abs btn" style="left:159px;top:1705px;width:135px;height:37px">Compare</a>
<div class="abs block-red" style="left:751px;top:1429px;width:185px;height:267px"></div>
<div class="abs" role="img" aria-label="Photo: man seen from behind looking at glowing stock market charts" style="left:780px;top:1498px;width:240px;height:284px;background:linear-gradient(180deg,#0f4f55 0%,#146b6b 45%,#1e5d7a 70%,#0d2f4a 100%)"></div>
<div class="abs tone-block" role="img" aria-label="Decorative diagonal line texture" style="left:894px;top:1696px;width:149px;height:111px"></div>

<!-- future -->
<div class="abs block-red" style="left:158px;top:1964px;width:193px;height:264px"></div>
<div class="abs" role="img" aria-label="Photo: city skyline at night overlaid with glowing network connections" style="left:197px;top:1875px;width:243px;height:316px;background:linear-gradient(180deg,#0a3fa0 0%,#1656c2 40%,#0c2e78 75%,#071a4a 100%)"></div>
<div class="abs tone-block" role="img" aria-label="Decorative diagonal line texture" style="left:440px;top:1960px;width:89px;height:134px"></div>
<div class="abs feature" style="left:643px;top:1920px;width:405px">
  <h2>The future is exciting</h2>
  <p>Let's make the electricity system smarter together. Vindgerdi uses artificial intelligence, data science and automation to minimize costs and promote eccentricity</p>
</div>
<a class="abs btn" style="left:646px;top:2031px;width:134px;height:37px">LEARN MORE</a>

<!-- footer -->
<footer class="footer">
  <div class="abs footer-bg"></div>
  <div class="abs email">Enter Email Address...</div>
  <a class="abs submit">SUBMIT NOW</a>

  <div class="abs brand"><span class="dot"></span>VINDGERDI</div>
  <p class="abs about">Our marketing strategy is to portray a tech company mindset and to show dedication to driving down the electricity price on the market.</p>

  <h3 class="abs col-title" style="left:338px">Site Map</h3>
  <ul class="abs links" style="left:338px;top:2523px;line-height:30px">
    <li>Home</li><li>Terms of Business</li><li>Question &amp; Answer</li><li>About Vindgerdi</li>
  </ul>

  <h3 class="abs col-title" style="left:612px">Contact Us</h3>
  <div class="abs contact-row" style="top:2514px">
    <span class="ico"><svg width="18" height="18" viewBox="0 0 24 24"><path fill="#9c2f33" d="M12 2a7 7 0 0 0-7 7c0 5 7 13 7 13s7-8 7-13a7 7 0 0 0-7-7zm0 9.5A2.5 2.5 0 1 1 12 6.5a2.5 2.5 0 0 1 0 5z"/></svg></span>
    <span>Hafnargata 22, 200 Kópavogur</span>
  </div>
  <div class="abs contact-row" style="top:2566px">
    <span class="ico"><svg width="18" height="18" viewBox="0 0 24 24"><path fill="#9c2f33" d="M3 5h18v14H3z"/><path fill="none" stroke="#fff" stroke-width="1.8" d="M3 6l9 7 9-7"/></svg></span>
    <span>info@vindgerdi-example.is</span>
  </div>
  <div class="abs contact-row" style="top:2622px">
    <span class="ico"><svg width="18" height="18" viewBox="0 0 24 24"><path fill="#9c2f33" d="M6.6 10.8a15 15 0 0 0 6.6 6.6l2.2-2.2a1 1 0 0 1 1-.25 11.4 11.4 0 0 0 3.6.6 1 1 0 0 1 1 1V20a1 1 0 0 1-1 1A17 17 0 0 1 3 4a1 1 0 0 1 1-1h3.5a1 1 0 0 1 1 1c0 1.25.2 2.45.6 3.6a1 1 0 0 1-.25 1z"/></svg></span>
    <span>555-0199</span>
  </div>

  <h3 class="abs col-title" style="left:888px">Terms of Business</h3>
  <ul class="abs links" style="left:888px;top:2519px;line-height:22.5px">
    <li>Scope</li><li>Gathering information and plan</li><li>Dealer change</li><li>User exchange</li><li>Prices and payment terms</li><li>End of contractual relationship</li><li>Privacy</li><li>Uncontrollable events</li>
  </ul>

  <div class="abs copyright">©2021 VINDGERDI - All Right Reserved.</div>
</footer>

</body>
</html>
```